Zelvo Stationary

Design the stationary of Zelvo Promotions Group.

Zelvo is a BTL company, BTL meaning "below the line". In other words Zelvo is a Promotional Marketing company (the company that design the brands promotional activities).

The design should transmit creativity, agility, boldness.

I need:
* Bis Card
* Letter head
* Envelopes, both vertical and horizontal (for legal size), and letter envelope
* Folders
* PPT template (Title page and regular page)
* CD slip (CD envelope)
* ID card (employee card)

And what ever else you want to throw in.
Updates

Guys,

Something I missed from the brief.   The predominat color should be RED.

Also, have fun and play with the exclamation mark (!) of the logo. 

Hi guys, more comments:

Remember that Zelvo is a "creativity" agency, not in the advertising side but on the promotional side, and that should reflect on the stationary.

 I want a bold design.  Bold and yet crisp.

 

Guys, i just uploaded the Logo in AI format.

I Also uploaded the actual Zelvo Bis Card, wich I like.  So I will like to see some designs with that bis card approach.

Guys, I am so sorry, but I notice in your last post that I upladed a wrong design ("13154_promotions_group_zelvo_brief225630.ai").  The problem was that I asked the designer the file in AI format and he send me thw wrong file, and since I dont have Illustrator I could not verify it.

The differences are minor, I just already ask him the correct one (similar to the EPS file).

Sorry                                   

Just post the correct AI file : "Zelvo Logo.ai"

Reason: I'm expecting more designs to choose from and also I wont be available tomorrow to decide.

Reason: Sorry guys, but we are not there yet!

Target Market(s)

Marketing directors, Marketing Managers

Industry/Entity Type

Legal

Requirements
Must have
• Must work with the logo attached.
The predominat color should be RED.
Play and have fun with the exclamation mark (!).
Should not have
• * No old fonts

Should not be:
* boring
* Informal
* rigid

```html
<!DOCTYPE html>
<html lang="en">
<head>
<meta charset="utf-8">
<title>Zelvo Promotions Group – Business Card</title>
<link rel="stylesheet" href="https://fonts.googleapis.com/css2?family=Arimo:wght@400;700&family=Jost:wght@400;500;600;700&display=swap">
<style>
  :root {
    --page-bg: #ecebe8;
    --brand-red: #b3161f;
    --brand-red-dark: #7d0d13;
    --brand-red-light: #c9202a;
    --ink: #2a2a2a;
    --ink-soft: #444;
    --card-white: #ffffff;
    --card-grey: #e9e9e9;
    --swoosh-grey: #8c8c8c;
    --swoosh-dark: #3a3a3a;
  }
  * { margin: 0; padding: 0; box-sizing: border-box; }
  html, body { width: 1200px; height: 900px; overflow: hidden; }
  body {
    background: var(--page-bg);
    font-family: "Jost", "Helvetica Neue", sans-serif;
    position: relative;
  }
  .card {
    position: absolute;
    width: 520px;
    height: 297px;
    border-radius: 22px;
    overflow: hidden;
    box-shadow: 0 10px 28px rgba(0,0,0,.18);
  }
  /* Front */
  .card-front {
    left: 100px; top: 110px;
    background: radial-gradient(ellipse at 45% 40%, var(--brand-red-light) 0%, var(--brand-red) 55%, var(--brand-red-dark) 100%);
    color: #fff;
  }
  .card-front .brand {
    position: absolute;
    left: 0; right: 0; top: 118px;
    display: flex; justify-content: center; align-items: center; gap: 12px;
  }
  .brand-name {
    font-family: "Jost", sans-serif;
    font-weight: 700;
    font-size: 30px;
    letter-spacing: .5px;
    white-space: nowrap;
  }
  .brand-dot {
    width: 16px; height: 16px; border-radius: 50%;
  }
  .card-front .brand-name { color: #fff; }
  .card-front .brand-dot { background: #fff; }
  .website {
    position: absolute; left: 0; right: 0; bottom: 26px;
    text-align: center;
    font-size: 13px; letter-spacing: .4px;
  }
  /* Back */
  .card-back {
    left: 580px; top: 490px;
    background: linear-gradient(160deg, var(--card-white) 40%, var(--card-grey) 100%);
    color: var(--ink);
  }
  .card-back .brand {
    position: absolute; right: 30px; top: 66px;
    display: flex; align-items: center; gap: 8px;
  }
  .card-back .brand-name { color: var(--ink); font-size: 19px; }
  .card-back .brand-dot { background: var(--brand-red); width: 12px; height: 12px; }
  .person {
    position: absolute; left: 34px; top: 66px;
    font-family: "Arimo", sans-serif;
  }
  .person-name { color: var(--brand-red); font-weight: 700; font-size: 21px; line-height: 1.1; }
  .person-role { color: var(--ink-soft); font-size: 13px; margin-top: 4px; }
  .contact-line {
    display: flex; align-items: center; gap: 6px;
    font-size: 14px; color: var(--ink); line-height: 19px;
  }
  .contact-line svg { width: 13px; height: 13px; flex: none; fill: var(--brand-red); }
  .address {
    position: absolute; left: 44px; top: 162px;
    font-size: 14px; font-weight: 500; color: var(--ink); line-height: 18px;
  }
  .address .contact-line { font-weight: 400; }
  .swoosh { position: absolute; left: 0; bottom: 0; width: 520px; height: 297px; }
</style>
</head>
<body>

<section class="card card-front" aria-label="Business card front">
  <div class="brand">
    <span class="brand-name">Zelvo Promotions Group</span>
    <span class="brand-dot"></span>
  </div>
  <p class="website">www.zelvo.com</p>
</section>

<section class="card card-back" aria-label="Business card back">
  <svg class="swoosh" viewBox="0 0 520 297" preserveAspectRatio="none" aria-hidden="true">
    <defs>
      <linearGradient id="greyBand" x1="0" x2="1" y1="0" y2="0">
        <stop offset="0" stop-color="#d8d8d8"/>
        <stop offset="0.6" stop-color="var(--swoosh-grey)"/>
        <stop offset="1" stop-color="var(--swoosh-dark)"/>
      </linearGradient>
      <linearGradient id="redBand" x1="0" x2="1" y1="0" y2="0">
        <stop offset="0" stop-color="var(--brand-red)"/>
        <stop offset="0.7" stop-color="var(--brand-red-light)"/>
        <stop offset="1" stop-color="var(--brand-red)" stop-opacity="0"/>
      </linearGradient>
    </defs>
    <path d="M0 262 C 180 262, 380 230, 520 150 L 520 297 L 0 297 Z" fill="url(#greyBand)"/>
    <path d="M0 270 C 180 270, 360 245, 470 215 C 360 262, 200 285, 0 297 Z" fill="#fff"/>
    <path d="M0 276 C 170 276, 330 258, 430 232 C 330 275, 180 297, 0 297 Z" fill="url(#redBand)"/>
  </svg>

  <div class="person">
    <p class="person-name">Your Name</p>
    <p class="person-role">Position</p>
    <p class="contact-line">
      <svg viewBox="0 0 12 12"><path d="M3 0h6a1 1 0 0 1 1 1v10a1 1 0 0 1-1 1H3a1 1 0 0 1-1-1V1a1 1 0 0 1 1-1zm0 1.5v7.5h6V1.5zM6 9.8a.7.7 0 1 0 0 1.4.7.7 0 0 0 0-1.4z"/></svg>
      (123) 456 7890
    </p>
  </div>

  <div class="brand">
    <span class="brand-name">Zelvo Promotions Group</span>
    <span class="brand-dot"></span>
  </div>

  <div class="address">
    <p>123, Your Street,</p>
    <p>Your City, Country, 123.</p>
    <p class="contact-line">
      <svg viewBox="0 0 12 12"><path d="M1 3.5C1 2 3 1.5 6 1.5S11 2 11 3.5v1H8.5v-1h-5v1H1zM2 6l2-1.5h4L10 6v4.5H2zm4 .8a1.5 1.5 0 1 0 0 3 1.5 1.5 0 0 0 0-3z"/></svg>
      (123) 456 7890
    </p>
    <p class="contact-line">
      <svg viewBox="0 0 12 12"><path d="M1 3.5C1 2 3 1.5 6 1.5S11 2 11 3.5v1H8.5v-1h-5v1H1zM2 6h8v4.5H2zm1.5 1v1h5V7zm0 2v.8h5V9z"/></svg>
      (123) 456 7890
    </p>
    <p class="contact-line">
      <svg viewBox="0 0 12 12"><path d="M0.5 2.5h11v7h-11zm1.2 1L6 6.6l4.3-3.1zm-.2 1.1v4h9v-4L6 7.8z"/></svg>
      info@zelvo.com
    </p>
  </div>
</section>

</body>
</html>
```